Small Business Broker Business Card Design

A business card design for a small business brokerage, which is a financial service, not unlike real estate brokerage, but for small businesses such as laundromats, pizza shops, restaurants, cleaners etc. The designs should all be simple, more conservative in nature, using the colors and font of the logo. Again, think real estate Brokerage as a business context
Contact Information for Business Card
Name: Glen R. Harlow. Title: Small Business Advisor. Email: g.harlow@bayfieldcapitalworks.example. Mobile: (555) 274-3918. Office: (555) 806-2147. www.bayfieldcapitalworks.example

```html
<!DOCTYPE html>
<html lang="en">
<head>
<meta charset="utf-8">
<title>Bayfield Capital Works – Business Card</title>
<link href="https://fonts.googleapis.com/css2?family=Montserrat:wght@400;500;600;700;800&display=swap" rel="stylesheet">
<style>
  :root {
    --navy: #1d3a72;
    --navy-deep: #172f5e;
    --green: #8cc63f;
    --white: #ffffff;
    --ink: #1d3a72;
    --backdrop: #e6e8ec;
  }
  * { box-sizing: border-box; margin: 0; padding: 0; }
  html, body { width: 1200px; height: 800px; overflow: hidden; }
  body {
    background: var(--backdrop);
    font-family: "Montserrat", Arial, sans-serif;
    display: flex;
    align-items: center;
    justify-content: center;
    gap: 40px;
  }
  .card {
    width: 540px;
    height: 309px;
    border-radius: 16px;
    overflow: hidden;
    position: relative;
    box-shadow: 0 6px 18px rgba(0,0,0,0.18);
  }

  /* Back side */
  .card-back { background: var(--navy); }
  .card-back .pattern {
    position: absolute; inset: 0;
    background: linear-gradient(135deg, var(--navy-deep) 0%, var(--navy) 55%, #2a4a86 100%);
  }
  .card-back .lockup {
    position: absolute; left: 0; right: 0; top: 50%;
    transform: translateY(-50%);
    text-align: center;
  }
  .card-back .company-row { display: inline-flex; align-items: center; gap: 10px; }
  .card-back .brand-square { width: 16px; height: 16px; background: var(--green); }
  .card-back .company-name {
    color: var(--white); font-weight: 700; font-size: 20px; letter-spacing: 0.5px;
  }
  .card-back .tagline {
    color: var(--green); font-weight: 600; font-size: 9.5px; letter-spacing: 1.4px;
    margin-top: 6px; text-transform: uppercase;
  }

  /* Front side */
  .card-front { background: var(--white); }
  .card-front .lockup { position: absolute; left: 32px; top: 40px; right: 28px; }
  .card-front .company-row { display: flex; align-items: center; gap: 10px; }
  .card-front .brand-square { width: 22px; height: 22px; background: var(--navy); flex: none; }
  .card-front .company-name {
    color: var(--navy); font-weight: 700; font-size: 25px; letter-spacing: 0.3px; white-space: nowrap;
  }
  .card-front .tagline {
    color: var(--green); font-weight: 600; font-size: 10.5px; letter-spacing: 1.5px;
    text-transform: uppercase; margin-top: 6px; margin-left: 32px;
  }
  .card-front .details {
    position: absolute; left: 32px; right: 24px; top: 132px;
    display: flex; align-items: center;
  }
  .person { width: 206px; }
  .person-name { color: var(--navy); font-weight: 800; font-size: 22px; }
  .person-title { color: var(--ink); font-weight: 500; font-size: 12px; margin-top: 3px; }
  .divider { width: 1px; height: 96px; background: var(--navy); margin-right: 16px; }
  .contacts { list-style: none; }
  .contacts li {
    display: flex; align-items: center; gap: 9px;
    color: var(--ink); font-size: 11px; font-weight: 500; line-height: 22px;
  }
  .contacts svg { width: 12px; height: 12px; fill: var(--navy); flex: none; }
  .address-band {
    position: absolute; left: 0; right: 0; bottom: 0; height: 44px;
    background: var(--navy); color: var(--white);
    font-size: 12px; font-weight: 500; letter-spacing: 0.3px;
    display: flex; align-items: center; justify-content: center;
  }
</style>
</head>
<body>

  <section class="card card-back" aria-label="Business card back">
    <div class="pattern" role="img" aria-label="Tonal navy background pattern"></div>
    <div class="lockup">
      <div class="company-row">
        <span class="brand-square"></span>
        <span class="company-name">BAYFIELD CAPITAL WORKS, INC</span>
      </div>
      <p class="tagline">Confidently buy or sell a local business today</p>
    </div>
  </section>

  <section class="card card-front" aria-label="Business card front">
    <div class="lockup">
      <div class="company-row">
        <span class="brand-square"></span>
        <span class="company-name">BAYFIELD CAPITAL WORKS, INC</span>
      </div>
      <p class="tagline">Confidently buy or sell a local business today</p>
    </div>

    <div class="details">
      <div class="person">
        <p class="person-name">Glen R. Harlow</p>
        <p class="person-title">Small Business Advisor</p>
      </div>
      <span class="divider"></span>
      <ul class="contacts">
        <li>
          <svg viewBox="0 0 24 24" aria-hidden="true"><path d="M3 8c0-2 2-4 9-4s9 2 9 4v2h-5V8H8v2H3zM5 12h14l2 8H3z"/></svg>
          (555) 806-2147
        </li>
        <li>
          <svg viewBox="0 0 24 24" aria-hidden="true"><path d="M6.6 10.8a15.1 15.1 0 0 0 6.6 6.6l2.2-2.2c.3-.3.7-.4 1-.2 1.1.4 2.3.6 3.6.6.6 0 1 .4 1 1V20c0 .6-.4 1-1 1A17 17 0 0 1 3 4c0-.6.4-1 1-1h3.5c.6 0 1 .4 1 1 0 1.3.2 2.5.6 3.6.1.3 0 .7-.2 1z"/></svg>
          (555) 274-3918
        </li>
        <li>
          <svg viewBox="0 0 24 24" aria-hidden="true"><path d="M2 5h20v14H2zm2 2v.5l8 5 8-5V7z"/></svg>
          g.harlow@bayfieldcapitalworks.example
        </li>
        <li>
          <svg viewBox="0 0 24 24" aria-hidden="true"><path d="M12 2a10 10 0 1 0 0 20 10 10 0 0 0 0-20zm6.9 6h-3a15 15 0 0 0-1.3-3.9A8 8 0 0 1 18.9 8zM12 4c.8 1.2 1.5 2.5 1.9 4h-3.8c.4-1.5 1.1-2.8 1.9-4zM4.3 14a8 8 0 0 1 0-4h3.4a16 16 0 0 0 0 4zm.8 2h3a15 15 0 0 0 1.3 3.9A8 8 0 0 1 5.1 16zm3-8h-3a8 8 0 0 1 4.3-3.9A15 15 0 0 0 8.1 8zM12 20c-.8-1.2-1.5-2.5-1.9-4h3.8c-.4 1.5-1.1 2.8-1.9 4zm2.3-6H9.7a14 14 0 0 1 0-4h4.6a14 14 0 0 1 0 4zm.3 5.9c.6-1.2 1-2.5 1.3-3.9h3a8 8 0 0 1-4.3 3.9zM16.3 14a16 16 0 0 0 0-4h3.4a8 8 0 0 1 0 4z"/></svg>
          www.bayfieldcapitalworks.example
        </li>
      </ul>
    </div>

    <div class="address-band">1480 SE Harbor Crest Blvd Stuart, Florida 34990</div>
  </section>

</body>
</html>
```